We’re a real estate firm that has landed a big builder in a neighboring state. Our branding needs...

We are a real estate firm who represents various builders along with doing resale here in Oregon. Our firm is growing to represent a big builder in Washington State and we’ll have another 40 brokers on our team. We need rebranding. As in, a new logo ( the house logo we have now looks cartoonish, hate it). We need new cards, something to really stand out. I’ve been thinking of using those NFC cards from ZEP or the ones with the seam color. I likely want two or three designs, a darker (as in a background color of black or grey) , a light one ( again I mean background color) and a credit card style (either plastic w an embossed name/number on front, or metal ). I’m thinking dark background for cc, or silver if it’s metal. That’s my thoughts, but you are the artists, so maybe you have an idea I haven’t considered. Our colors were black and red, but we don’t have to stick to that. Just nothing too busy. Oh, and we are typically representing the local, higher quality builders in our area (just below custom), but not national. Subdivisions are near the Kell Varney, Brisco, and Thornfield Crest sites. We are super excited, but without a lot of time to change the “look” of our brokerage. So I’ll be deciding and moving forward within 24 hours tops. Our name is Real Estate Summit Alliance ( we cant change the name because of timeline and business license) Thank you!

Industry/Entity Type

Real Estate

Contact Information for Business Card

The usual. Name of firm. Name of cardholder. Contact info.

Font styles to use
Serif
Sans Serif

Colors

Designer to choose colors to be used in the design.

Requirements
Must have
• A sleek or simple look. I included photos of cards with stylistic attributes we like. Thank you
Nice to have
• We really like the black backgrounds. With foil or embossed detail. We also like the black on black. Matte black card with raised shiny black detail. But still eye catching.
Should not have
• No ornate or busy looking style. We don’t want anything cluttered.

```html
<!DOCTYPE html>
<html lang="en">
<head>
<meta charset="utf-8">
<title>Real Estate Summit Alliance – Business Card</title>
<link rel="stylesheet" href="https://fonts.googleapis.com/css2?family=Open+Sans:wght@400;600&display=swap">
<style>
  :root {
    --page-bg: #151516;
    --card-bg: #1d1d1e;
    --card-edge: #262628;
    --emboss: #2c2c2e;
    --brand-blue: #1766c9;
    --text-light: #e6e6e6;
    --rule: #3a3a3d;
  }
  * { box-sizing: border-box; margin: 0; padding: 0; }
  html, body { width: 1200px; height: 900px; overflow: hidden; }
  body {
    background: var(--page-bg);
    font-family: "Open Sans", Arial, sans-serif;
    position: relative;
  }
  .card {
    position: absolute;
    left: 285px;
    width: 630px;
    height: 360px;
    background: var(--card-bg);
    border: 1px solid var(--card-edge);
    border-radius: 22px;
  }
  .card--back { top: 70px; }
  .card--front { top: 470px; }

  /* Back */
  .back-name {
    position: absolute;
    top: 100px; left: 0; right: 0;
    text-align: center;
    font-weight: 600;
    font-size: 46px;
    line-height: 54px;
    color: var(--emboss);
  }
  .back-web {
    position: absolute;
    top: 262px; left: 0; right: 0;
    text-align: center;
    font-size: 14px;
    letter-spacing: 1.5px;
    color: var(--text-light);
  }

  /* Front */
  .brand {
    position: absolute;
    top: 40px; right: 44px;
    display: flex;
    align-items: center;
    gap: 14px;
  }
  .brand-square {
    width: 18px; height: 18px;
    background: var(--brand-blue);
  }
  .brand-name {
    text-align: right;
    font-weight: 600;
    font-size: 30px;
    line-height: 36px;
    color: var(--brand-blue);
  }
  .divider {
    position: absolute;
    top: 170px; left: 300px; right: 44px;
    height: 1px;
    background: var(--rule);
  }
  .holder {
    position: absolute;
    left: 44px; top: 178px;
  }
  .holder-name {
    font-weight: 600;
    font-size: 21px;
    color: var(--brand-blue);
    letter-spacing: 0.5px;
  }
  .holder-role {
    font-size: 17px;
    color: var(--text-light);
    margin-top: -2px;
  }
  .contacts {
    position: absolute;
    left: 44px; top: 248px;
    list-style: none;
  }
  .contacts li {
    display: flex;
    align-items: center;
    gap: 10px;
    font-size: 17px;
    color: var(--text-light);
    line-height: 26px;
  }
  .contacts svg { width: 14px; height: 14px; fill: var(--brand-blue); }
  .address {
    position: absolute;
    right: 44px; top: 190px;
    text-align: right;
    font-size: 16px;
    line-height: 22px;
    font-style: normal;
    color: var(--text-light);
  }
</style>
</head>
<body>

<section class="card card--back" aria-label="Card back">
  <div class="back-name">Real Estate<br>Summit Alliance</div>
  <div class="back-web">WWW.RESUMMIT.EXAMPLE</div>
</section>

<section class="card card--front" aria-label="Card front">
  <div class="brand">
    <span class="brand-square" aria-hidden="true"></span>
    <div class="brand-name">Real Estate<br>Summit Alliance</div>
  </div>

  <div class="divider"></div>

  <div class="holder">
    <div class="holder-name">DANA WHITCOMBE</div>
    <div class="holder-role">Managing Director</div>
  </div>

  <ul class="contacts">
    <li>
      <svg viewBox="0 0 16 16" aria-hidden="true"><path d="M3 1h3l1.5 4-2 1.2a9 9 0 0 0 4.3 4.3L11 8.5l4 1.5v3a2 2 0 0 1-2 2A13 13 0 0 1 1 3a2 2 0 0 1 2-2z"/></svg>
      503-555 0147
    </li>
    <li>
      <svg viewBox="0 0 16 16" aria-hidden="true"><path d="M4.5 0h7A1.5 1.5 0 0 1 13 1.5v13a1.5 1.5 0 0 1-1.5 1.5h-7A1.5 1.5 0 0 1 3 14.5v-13A1.5 1.5 0 0 1 4.5 0zM5 2v10h6V2zm3 11a1 1 0 1 0 0 2 1 1 0 0 0 0-2z"/></svg>
      503-555 0148
    </li>
    <li>
      <svg viewBox="0 0 16 16" aria-hidden="true"><path d="M0 3h16v1.2L8 9 0 4.2zM0 5.8l8 4.8 8-4.8V13H0z"/></svg>
      hello@resummit.example
    </li>
  </ul>

  <address class="address">
    12345, Address Goes Here<br>
    Country Name, 123456
  </address>
</section>

</body>
</html>
```